Meridale Real Estate

We are looking for help with web design for a new company that is revolutionizing the real estate world on the listing side: by charing per hour for top level professional real estate services. We would like the concept to be simple, clean and easily understood.
Updates

We want this website to actually function, not just a static design.

Industry/Entity Type

Real Estate

```html
<!DOCTYPE html>
<html lang="en">
<head>
<meta charset="utf-8">
<title>Kestrel Partners — Meridale Real Estate</title>
<link rel="stylesheet" href="https://fonts.googleapis.com/css2?family=Crimson+Text:wght@400;600&family=Open+Sans:ital,wght@0,300;0,400;0,600;0,700;1,400&display=swap">
<style>
:root{
  --black:#000;
  --gold:#d9a32a;
  --gold-light:#e6b53a;
  --gold-dark:#c07a12;
  --gold-text:#c8871e;
  --white:#fff;
  --grey-bg:#f6f6f6;
  --card-border:#e2e2e2;
  --body-text:#555;
  --muted:#888;
  --footer-top:#2c2c2c;
  --footer-bottom:#141414;
}
*{box-sizing:border-box;margin:0;padding:0}
html,body{width:1200px;height:2190px;overflow:hidden}
body{font-family:"Open Sans",Arial,sans-serif;background:var(--white);color:var(--body-text);position:relative}

.site-header{height:105px;background:var(--black);position:relative}
.brand{position:absolute;left:110px;top:26px;display:flex;align-items:center;gap:12px}
.brand-mark{width:52px;height:52px;border-radius:50%;border:2px solid var(--gold)}
.brand-name{font-family:"Crimson Text",serif;font-size:22px;color:var(--gold);font-weight:400}
.call-us{position:absolute;right:104px;top:32px;text-align:right}
.call-us-label{color:var(--white);font-size:15px;letter-spacing:.3px}
.call-us-number{color:var(--gold);font-size:22px;font-weight:600;margin-top:2px}

.main-nav{height:51px;background:linear-gradient(var(--gold-light),var(--gold-dark));display:flex;justify-content:center;padding-left:18px}
.main-nav a{color:var(--white);text-decoration:none;font-size:15px;font-weight:600;line-height:51px;padding:0 21px;border-right:1px solid rgba(255,255,255,.35)}
.main-nav a:first-child{border-left:0}
.main-nav a:last-child{border-right:0}

.hero{height:439px;position:relative;overflow:hidden}
.hero-photo{position:absolute;inset:0;background:
  radial-gradient(ellipse at 65% 40%,#e9ecf3 0%,#c9c3d3 18%,transparent 40%),
  linear-gradient(180deg,#203a7a 0%,#3c5aa8 35%,#c98e86 62%,#3b2a30 78%,#1b1a22 100%)}
.hero-caption{position:absolute;left:100px;top:126px;width:455px;height:160px;background:rgba(15,15,20,.82);clip-path:polygon(0 0,100% 0,83% 100%,0 100%);padding:18px 0 0 33px}
.hero-title{font-family:"Crimson Text",serif;color:var(--gold-light);font-size:42px;line-height:1}
.hero-sub{font-family:"Crimson Text",serif;color:var(--white);font-size:24px;margin-top:6px}
.hero-text{color:#9a9a9a;font-size:12px;line-height:19px;margin-top:6px;width:350px}
.hero-dots{position:absolute;left:572px;top:413px;display:flex;gap:4px}
.hero-dots span{width:17px;height:17px;border-radius:50%;background:#333}

.welcome{height:202px;text-align:center;padding-top:34px}
.welcome h1{font-family:"Crimson Text",serif;font-weight:400;color:#111;font-size:34px}
.welcome p{font-size:12.5px;line-height:21px;color:#444;width:1000px;margin:8px auto 0}
.welcome p+p{margin-top:4px}

.destinations{height:778px;background:var(--grey-bg);border-top:1px solid #e8e8e8;padding-top:26px}
.section-title{font-family:"Crimson Text",serif;font-weight:400;text-align:center;font-size:34px;color:var(--gold-text)}
.dest-grid{display:grid;grid-template-columns:repeat(4,242px);gap:11px 11px;width:1001px;margin:22px auto 0}
.dest-card{height:210px;background:var(--white);border:1px solid var(--card-border);padding:9px 9px 0}
.dest-photo{height:112px}
.dest-card h3{font-size:15px;font-weight:600;color:var(--gold-text);margin:10px 0 2px 4px}
.dest-card p{font-size:11.5px;line-height:19px;color:#999;margin-left:4px}
.ph-alps{background:linear-gradient(#2d5aa8,#9fb4d6 45%,#e8eef5 70%,#6f7f90)}
.ph-amsterdam{background:linear-gradient(#5a2aa0,#8c3a4a 55%,#d48a3a)}
.ph-bahamas{background:linear-gradient(#3fa6e4,#bfe8f5 55%,#f3ecd8)}
.ph-cannes{background:linear-gradient(#2f7fd1,#e9e2d0 55%,#3a8fc0)}
.ph-ny{background:linear-gradient(#9fc2e6,#7a8796 60%,#4e5a66)}
.ph-hampton{background:linear-gradient(#b9d0ea,#5d8a3a 45%,#a0772e)}
.ph-ibiza{background:linear-gradient(#2a7bc4,#e9eef2 50%,#1d62a8)}
.ph-vegas{background:linear-gradient(#1a2a5a,#c8762a 60%,#3a2a3a)}
.ph-london{background:linear-gradient(#0d3d7a,#1b5a9a 55%,#0c1a2a)}
.ph-la{background:linear-gradient(#e0a84a,#b87a3a 55%,#5a4030)}
.ph-marbella{background:linear-gradient(#6aa4d8,#e8eef4 60%,#3a6a90)}
.ph-miami{background:linear-gradient(#2e7fd6,#cfe3f3 55%,#e8dcc0)}

.testimonials{height:308px;background:linear-gradient(var(--gold) 0%,#d69a22 50%,var(--gold-dark) 100%);position:relative;padding-top:34px}
.testimonials .section-title{color:var(--white);font-family:"Open Sans",sans-serif;font-size:25px}
.testimonial-row{display:flex;width:1000px;margin:30px auto 0;padding-left:8px}
.testimonial{width:340px;display:flex;gap:14px;padding-right:16px;border-right:1px solid rgba(255,255,255,.2)}
.testimonial:last-child{border-right:0}
.testimonial + .testimonial{padding-left:14px}
.avatar{flex:0 0 90px;height:90px;border-radius:50%;border:4px solid var(--white);margin-top:6px}
.av-1{background:linear-gradient(135deg,#4a78b0,#d7b28a)}
.av-2{background:linear-gradient(135deg,#cfcfcf,#8c8c8c)}
.av-3{background:linear-gradient(135deg,#3a5fa0,#b8a890)}
.quote{font-style:italic;font-size:12px;line-height:19px;color:var(--white)}
.author{font-size:12px;font-weight:600;color:var(--white);margin-top:14px}
.slider-arrows{position:absolute;right:80px;bottom:28px}

.site-footer{height:248px;background:linear-gradient(var(--footer-top),var(--footer-bottom));padding:34px 0 0 104px;display:flex}
.footer-col{color:#cfcfcf}
.footer-col h4{font-weight:300;font-size:20px;color:#e8e8e8;margin-bottom:6px}
.footer-col a,.footer-col li{display:block;list-style:none;font-size:13px;line-height:26px;color:#cfcfcf;text-decoration:none}
.col-company{width:214px}
.col-support{width:197px}
.col-sublinks{width:216px}
.contact-list li{padding-left:4px}
.social{display:flex;gap:9px;margin-top:8px;padding-left:4px}
.social span{width:24px;height:24px;border-radius:3px}
.social .s1{background:#3b5a98}.social .s2{background:#3aa8df}.social .s3{background:#1f7bb6}.social .s4{background:#f08a1f}

.copyright{height:60px;background:var(--black);color:var(--white);font-family:Arial,sans-serif;font-size:12px;font-weight:700;padding:18px 0 0 104px}
</style>
</head>
<body>

<header class="site-header">
  <div class="brand">
    <span class="brand-mark"></span>
    <span class="brand-name">Meridale Real Estate</span>
  </div>
  <div class="call-us">
    <div class="call-us-label">CALL US NOW</div>
    <div class="call-us-number">+1-555-318-2760</div>
  </div>
</header>

<nav class="main-nav">
  <a href="#">HOME</a><a href="#">ABOUT</a><a href="#">DESTINATIONS</a><a href="#">CONCIERGE</a><a href="#">OWNERS &amp; AGENTS</a><a href="#">SALES</a><a href="#">SOCIAL</a><a href="#">CONTACT US</a>
</nav>

<section class="hero">
  <div class="hero-photo" role="img" aria-label="Curved white resort hotel at dusk with palm trees and a lit pool"></div>
  <div class="hero-caption">
    <div class="hero-title">Featured Properties</div>
    <div class="hero-sub">Suspendisse vulputate aliquam</div>
    <p class="hero-text">Etiam est nunc venenatis in tristique eu imperdiet ac nisl. Cum sociis natoque penatibus et magnis dis part</p>
  </div>
  <div class="hero-dots"><span></span><span></span><span></span></div>
</section>

<section class="welcome">
  <h1>Welcome to Kestrel Partners Mainpage</h1>
  <p>Kestrel Partners is everywhere you need to be! Short term rentals, vacation property rentals and property management are just some of the services we offer at Kestrel.</p>
  <p>Get access to both short &amp; long term property rentals at the best prices with top-notch support from our team. Browse through our variety of cities worldwide and find your perfectly furnished short term stay today. Our new Global Partners Program can now serve you better with our specialized local teams in each specific location.</p>
</section>

<section class="destinations">
  <h2 class="section-title">Top Destination</h2>
  <div class="dest-grid">
    <article class="dest-card"><div class="dest-photo ph-alps" role="img" aria-label="Snowy alpine peaks"></div><h3>Alps</h3><p>Morbi diam mauris viverra in gravida eu mattis in ante Morbi eget arc</p></article>
    <article class="dest-card"><div class="dest-photo ph-amsterdam" role="img" aria-label="Canal houses at night"></div><h3>Amsterdam</h3><p>Morbi diam mauris viverra in gravida eu mattis in ante Morbi eget arc</p></article>
    <article class="dest-card"><div class="dest-photo ph-bahamas" role="img" aria-label="White beach with turquoise sea"></div><h3>Bahamas</h3><p>Morbi diam mauris viverra in gravida eu mattis in ante Morbi eget arc</p></article>
    <article class="dest-card"><div class="dest-photo ph-cannes" role="img" aria-label="Coastal town along a bay"></div><h3>Cannes</h3><p>Morbi diam mauris viverra in gravida eu mattis in ante Morbi eget arc</p></article>
    <article class="dest-card"><div class="dest-photo ph-ny" role="img" aria-label="City skyline of skyscrapers"></div><h3>Corp NY Stay</h3><p>Morbi diam mauris viverra in gravida eu mattis in ante Morbi eget arc</p></article>
    <article class="dest-card"><div class="dest-photo ph-hampton" role="img" aria-label="Formal garden in front of a manor"></div><h3>Hampton</h3><p>Morbi diam mauris viverra in gravida eu mattis in ante Morbi eget arc</p></article>
    <article class="dest-card"><div class="dest-photo ph-ibiza" role="img" aria-label="White terrace above the sea"></div><h3>Ibiza</h3><p>Morbi diam mauris viverra in gravida eu mattis in ante Morbi eget arc</p></article>
    <article class="dest-card"><div class="dest-photo ph-vegas" role="img" aria-label="City strip lit at night"></div><h3>Las Vegas</h3><p>Morbi diam mauris viverra in gravida eu mattis in ante Morbi eget arc</p></article>
    <article class="dest-card"><div class="dest-photo ph-london" role="img" aria-label="Square with fountain at night"></div><h3>London</h3><p>Morbi diam mauris viverra in gravida eu mattis in ante Morbi eget arc</p></article>
    <article class="dest-card"><div class="dest-photo ph-la" role="img" aria-label="Downtown towers at sunset"></div><h3>Los Angeles</h3><p>Morbi diam mauris viverra in gravida eu mattis in ante Morbi eget arc</p></article>
    <article class="dest-card"><div class="dest-photo ph-marbella" role="img" aria-label="Marina with white yachts"></div><h3>Marbella</h3><p>Morbi diam mauris viverra in gravida eu mattis in ante Morbi eget arc</p></article>
    <article class="dest-card"><div class="dest-photo ph-miami" role="img" aria-label="Lifeguard hut on a sunny beach"></div><h3>Maimi Beach</h3><p>Morbi diam mauris viverra in gravida eu mattis in ante Morbi eget arc</p></article>
  </div>
</section>

<section class="testimonials">
  <h2 class="section-title">Customer Testimonials</h2>
  <div class="testimonial-row">
    <div class="testimonial"><div class="avatar av-1" role="img" aria-label="Keys held out in front of a house"></div><div><p class="quote">Malesuada nec ultricies sit amet porttitor mattis enim In massa libero interdum nec interdum vel blandit sed nulla In ullamcorper est eget tempor cursus</p><p class="author">By Author Name</p></div></div>
    <div class="testimonial"><div class="avatar av-2" role="img" aria-label="Soft-focus house interior"></div><div><p class="quote">Malesuada nec ultricies sit amet porttitor mattis enim In massa libero interdum nec interdum vel blandit sed nulla In ullamcorper est eget tempor cursus</p><p class="author">By Author Name</p></div></div>
    <div class="testimonial"><div class="avatar av-3" role="img" aria-label="Small model house held in a hand"></div><div><p class="quote">Malesuada nec ultricies sit amet porttitor mattis enim In massa libero interdum nec interdum vel blandit sed nulla In ullamcorper est eget tempor cursus</p><p class="author">By Author Name</p></div></div>
  </div>
  <svg class="slider-arrows" width="34" height="22" viewBox="0 0 34 22" aria-label="Previous and next">
    <path d="M10 2 L2 11 L10 20" fill="none" stroke="#fff" stroke-width="2.2"/>
    <path d="M24 2 L32 11 L24 20" fill="none" stroke="#fff" stroke-width="2.2"/>
  </svg>
</section>

<footer class="site-footer">
  <div class="footer-col col-company"><h4>Company</h4><a href="#">About</a><a href="#">Destinations</a><a href="#">Concierge</a><a href="#">Owners &amp; Agents</a><a href="#">Sales</a></div>
  <div class="footer-col col-support"><h4>Support</h4><a href="#">Social</a><a href="#">Services</a><a href="#">Contact Us</a></div>
  <div class="footer-col col-sublinks"><h4>Sub links</h4><a href="#">Testimonials</a><a href="#">Recent Blog</a><a href="#">Clients &amp; Partners</a><a href="#">Newsletters</a></div>
  <div class="footer-col col-contact"><h4>Contact Us</h4>
    <ul class="contact-list"><li>48 Linden Row,</li><li>3rd Floor, Brookfield, NY 10990</li><li>Tel: +1 (555) 204-7713</li><li>Email: booking@kestrelpartners.com</li></ul>
    <div class="social"><span class="s1"></span><span class="s2"></span><span class="s3"></span><span class="s4"></span></div>
  </div>
</footer>

<div class="copyright">© Copyrights 2015 Meridale Real Estate. All Right Reserved</div>

</body>
</html>
```